Moravel Aesthetic Doctor

I require an elegant, luxurious looking business card for my aesthetic business. I am a doctor and that will set me aside from competitors. I am planning to provide home and spa based treatments to clients with high expectations. I have attached my logo.

```html
<!DOCTYPE html>
<html lang="en">
<head>
<meta charset="utf-8">
<title>Moravel Aesthetic Doctor – Business Card</title>
<link rel="stylesheet" href="https://fonts.googleapis.com/css2?family=Marcellus&family=Open+Sans:wght@400;600&display=swap">
<style>
  :root {
    --backdrop: #3a3a3c;
    --card: #1c1c1e;
    --sky: #4fb3e8;
    --silver: #a8b2c2;
    --paper: #ffffff;
    --name: #b9c3d1;
    --groove: #0e0e10;
  }
  * { box-sizing: border-box; margin: 0; padding: 0; }
  html, body { width: 799px; height: 1200px; overflow: hidden; }
  body {
    background: var(--backdrop);
    font-family: "Open Sans", sans-serif;
    position: relative;
  }
  .card {
    position: absolute;
    left: 80px;
    width: 640px;
    height: 366px;
    background: var(--card);
    border-radius: 6px;
    overflow: hidden;
    box-shadow: 0 10px 30px rgba(0,0,0,.45);
  }
  .card--front { top: 90px; }
  .card--back { top: 720px; }

  .brand {
    position: absolute;
    left: 70px;
    top: 52px;
    display: flex;
    align-items: center;
    gap: 22px;
  }
  .card--back .brand { top: 40px; }
  .brand__mark {
    width: 88px; height: 88px;
    border-radius: 50%;
    background: var(--sky);
    flex: none;
  }
  .brand__name {
    font-family: "Marcellus", serif;
    font-weight: 400;
    color: var(--name);
    line-height: 1;
  }
  .brand__word { display: block; font-size: 58px; letter-spacing: 3px; }
  .brand__tag { display: block; font-size: 22px; letter-spacing: 3px; margin-top: 6px; padding-left: 6px; }

  .services {
    position: absolute;
    left: 0; right: 0;
    top: 214px;
    text-align: center;
    color: var(--paper);
    font-size: 16px;
    line-height: 1.45;
  }
  .band {
    position: absolute;
    left: 0; right: 0;
    top: 268px;
    height: 40px;
    background: var(--sky);
    color: var(--paper);
    font-size: 17px;
    letter-spacing: 1px;
    display: flex;
    align-items: center;
    justify-content: center;
  }

  .doctor {
    position: absolute;
    left: 44px;
    top: 142px;
  }
  .doctor__name {
    font-family: "Marcellus", serif;
    color: var(--silver);
    font-size: 21px;
    line-height: 1.3;
  }
  .doctor__post { font-family: "Open Sans", sans-serif; font-size: 10px; color: var(--sky); margin-left: 8px; }
  .doctor__diploma { color: var(--sky); font-size: 13px; line-height: 1.3; margin-top: 4px; }

  .waves { position: absolute; inset: 0; }

  .contact {
    position: absolute;
    right: 30px;
    bottom: 20px;
    list-style: none;
    color: var(--paper);
    font-size: 15px;
    text-align: right;
    line-height: 1.6;
  }
  .contact li { display: flex; justify-content: flex-end; align-items: center; gap: 10px; }
  .contact svg { width: 15px; height: 15px; flex: none; }
  .social-dot { width: 14px; height: 14px; border-radius: 50%; background: var(--paper); display: inline-block; }
</style>
</head>
<body>

<section class="card card--front">
  <div class="brand">
    <span class="brand__mark"></span>
    <h1 class="brand__name"><span class="brand__word">MORAVEL</span><span class="brand__tag">AESTHETIC DOCTOR</span></h1>
  </div>
  <p class="services">Dermal Injectables &nbsp;|&nbsp; Plasma Facials &nbsp;|&nbsp; Microneedling<br>Skin Boosters &nbsp;|&nbsp; Excessive Sweating</p>
  <div class="band">HOME AND SPA BASED TREATMENTS</div>
</section>

<section class="card card--back">
  <svg class="waves" viewBox="0 0 640 366" preserveAspectRatio="none" aria-hidden="true">
    <path d="M0,258 C120,270 250,342 400,320 S580,212 640,188 L640,366 L0,366 Z" fill="var(--sky)"/>
    <path d="M0,234 C120,244 250,318 400,298 S580,190 640,166" fill="none" stroke="var(--silver)" stroke-width="8"/>
    <path d="M0,246 C120,257 250,330 400,309 S580,201 640,177" fill="none" stroke="var(--groove)" stroke-width="3"/>
  </svg>
  <div class="brand">
    <span class="brand__mark"></span>
    <h2 class="brand__name"><span class="brand__word">MORAVEL</span><span class="brand__tag">AESTHETIC DOCTOR</span></h2>
  </div>
  <div class="doctor">
    <p class="doctor__name">Dr Elise Varga<span class="doctor__post">MRCPCH MD</span></p>
    <p class="doctor__diploma">Australasian Diploma of<br>Aesthetic Medicine</p>
  </div>
  <ul class="contact">
    <li>Follows: <span class="social-dot"></span><span class="social-dot"></span></li>
    <li>0800 555 014
      <svg viewBox="0 0 24 24"><path fill="#fff" d="M6.6 10.8a15 15 0 0 0 6.6 6.6l2.2-2.2c.3-.3.7-.4 1-.2 1.1.4 2.3.6 3.6.6.6 0 1 .4 1 1V20c0 .6-.4 1-1 1A17 17 0 0 1 3 4c0-.6.4-1 1-1h3.5c.6 0 1 .4 1 1 0 1.3.2 2.5.6 3.6.1.3 0 .7-.2 1z"/></svg>
    </li>
    <li>www.moravel.co.nz
      <svg viewBox="0 0 24 24"><rect x="3" y="6" width="18" height="12" fill="none" stroke="#fff" stroke-width="2"/><path d="M3 6l9 7 9-7" fill="none" stroke="#fff" stroke-width="2"/></svg>
    </li>
    <li>elise@moravel.co.nz
      <svg viewBox="0 0 24 24"><circle cx="12" cy="12" r="9" fill="none" stroke="#fff" stroke-width="2"/><path d="M3 12h18M12 3c3 3 3 15 0 18M12 3c-3 3-3 15 0 18" fill="none" stroke="#fff" stroke-width="1.6"/></svg>
    </li>
  </ul>
</section>

</body>
</html>
```